We need a complete design for our construction company KELTO CONSTRUCTION based in Auckland New Zealand, we need a logo, website, business card, vehicle design etc..
We are a mid to high-end construction company who work mostly on residential projects and some commercial.

What we want to see in the design;
Professional,
Architectural,
Simple,
Alternative,

We want the design to communicate professionalism, high quality wormanship and and quality service.

Target Market(s)

People looking for a quality building/ construction company

Industry/Entity Type

Construction Company

Contact Information for Business Card

KELTO CONSTRUCTION.co.nz
Lino Verasek
lino@keltoconstruction.example.nz
021 5807 462

Logo Text

KELTO CONSTRUCTION

Number of Pages Required

5+ page

Font styles to use
Sans Serif

Colors

Designer to choose colors to be used in the design.

Requirements
Must have
• Must appear high end, professional, quality, be simple, easy to use, give security to potential clients
Nice to have
• high-quality photos of our recent projects
• about us page
• blog page
• contact us page
• high quality content
Should not have
• should not be hard to use and have too much going on.

```html
<!DOCTYPE html>
<html lang="en">
<head>
<meta charset="utf-8">
<title>Kelto Construction</title>
<link href="https://fonts.googleapis.com/css2?family=Montserrat:wght@400;500;600;700&family=Lato:wght@400;700&display=swap" rel="stylesheet">
<style>
:root{
  --gold:#b8963e;
  --gold-light:#c9a756;
  --dark:#333333;
  --darker:#2a2a2a;
  --light:#f1f1f1;
  --tan:#d2ba84;
  --white:#ffffff;
  --text:#555555;
}
*{margin:0;padding:0;box-sizing:border-box}
html,body{width:1200px;height:3742px;overflow:hidden}
body{position:relative;background:var(--white);font-family:'Lato',sans-serif;color:var(--text)}
.abs{position:absolute}
h1,h2,h3{font-family:'Montserrat',sans-serif}
.gold{color:var(--gold)}

/* top bar */
.topbar{left:0;top:0;width:1200px;height:87px;background:var(--white)}
.contact-chip{top:16px;height:50px;display:flex;align-items:center;gap:14px;font-size:20px;color:var(--dark)}
.chip-icon{width:50px;height:50px;border-radius:50%;background:var(--gold);display:flex;align-items:center;justify-content:center}
.logo{left:470px;top:30px;width:260px;height:104px;background:var(--white);border:3px solid var(--gold);display:flex;flex-direction:column;align-items:center;justify-content:center;z-index:3;font-family:'Montserrat',sans-serif;font-weight:500;color:var(--gold);line-height:1.1}
.logo .big{font-size:42px;letter-spacing:6px}
.logo .small{font-size:15px;letter-spacing:5px}

/* nav */
.nav{left:0;top:87px;width:1200px;height:138px;background:var(--dark)}
.nav ul{list-style:none;position:absolute;left:77px;top:7px;display:flex;height:131px}
.nav li{font-family:'Montserrat',sans-serif;font-size:19px;color:var(--white);display:flex;align-items:center;padding:0 30px;margin-right:34px}
.nav li.active{background:var(--darker)}
.search{left:1058px;top:157px;width:42px;height:42px;border:2px solid var(--gold);display:flex;align-items:center;justify-content:center}

/* hero */
.hero{left:0;top:225px;width:1200px;height:678px;background:linear-gradient(180deg,#3c5a86 0%,#6a7c92 40%,#8b8272 75%,#5d574c 100%)}
.hero-title{left:0;width:1200px;top:424px;text-align:center;font-size:46px;font-weight:500;color:var(--white);letter-spacing:1px}
.hero-text{left:220px;width:760px;top:496px;text-align:center;font-size:16px;font-weight:700;color:var(--white);line-height:1.6}
.arrow-btn{width:40px;height:40px;background:var(--gold);display:flex;align-items:center;justify-content:center}

/* features */
.feature{color:var(--white);display:flex;gap:18px}
.feature h3{font-weight:400;font-size:18px;line-height:1.35;white-space:nowrap}
.feature p{font-size:14px;line-height:1.6;margin-top:6px}
.feature-icon{flex:none;width:62px;height:62px;border-radius:50%;background:var(--dark);margin-top:6px}
.band-text{left:77px;width:1046px;top:996px;text-align:center;font-family:'Montserrat',sans-serif;font-weight:700;font-size:20px;color:var(--white);letter-spacing:.5px}

/* welcome */
.welcome{left:0;top:1058px;width:1200px;height:422px;background:var(--light)}
.welcome-title{left:77px;top:1108px;font-size:36px;font-weight:400;color:var(--dark)}
.welcome-text{left:77px;top:1172px;width:710px;font-size:13.5px;line-height:2.05;color:var(--text)}
.btn{font-family:'Montserrat',sans-serif;font-size:18px;color:var(--white);display:flex;align-items:center;justify-content:center}
.btn-gold{background:var(--gold)}
.btn-dark{background:var(--dark)}
.welcome-art{left:863px;top:1125px;width:262px;height:262px;border-radius:50%;background:var(--white);box-shadow:0 4px 10px rgba(0,0,0,.25);display:flex;align-items:center;justify-content:center}
.welcome-art-fill{width:226px;height:226px;border-radius:50%;background:radial-gradient(circle at 50% 45%,#8fb8de 0%,#cfdce6 60%,#eef1f3 100%)}

/* projects */
.projects{left:0;top:1480px;width:1200px;height:219px;background:linear-gradient(90deg,#2e2e2e,#484540 70%,#3b3936)}
.kicker{left:77px;top:1540px;font-family:'Montserrat',sans-serif;font-size:19px;color:var(--white)}
.projects-title{left:77px;top:1582px;font-size:37px;font-weight:700;color:var(--white);letter-spacing:.5px}
.photo{top:1699px;width:300px;height:260px}

/* testimonials */
.testi{left:0;top:1959px;width:1200px;height:499px;background:#f5f5f5}
.section-title{left:0;width:1200px;text-align:center;font-size:36px;font-weight:400;color:var(--dark)}
.quote-box{width:62px;height:50px;background:var(--gold);color:var(--white);font-family:'Montserrat',sans-serif;font-size:60px;font-weight:700;line-height:70px;text-align:center}
.testi-text{font-size:14px;line-height:1.95;color:var(--white)}
.testi-name{font-family:'Montserrat',sans-serif;font-weight:700;font-size:14px;color:var(--white);margin-top:8px}
.dot{top:2368px;width:14px;height:14px;border-radius:50%;border:2px solid var(--gold)}

/* blog */
.blog-card h3{font-weight:400;font-size:21px;color:var(--white)}
.meta{display:flex;gap:34px;font-size:13px;color:var(--white);margin-top:14px;padding-top:14px;border-top:1px solid rgba(255,255,255,.55)}
.meta span{display:flex;align-items:center;gap:10px}
.meta i{display:inline-block;width:12px;height:12px;border-radius:50%}
.blog-card p{font-size:14px;line-height:1.8;color:var(--white);margin-top:16px}

/* cta */
.cta{left:0;top:3274px;width:1200px;height:154px;background:var(--gold)}
.cta-text{left:77px;top:3316px;width:820px;font-family:'Montserrat',sans-serif;font-size:25px;color:var(--white);line-height:1.3}

/* footer */
.footer{left:0;top:3428px;width:1200px;height:314px;background:var(--tan)}
.f-col{top:3460px;display:flex;flex-direction:column;align-items:center;gap:10px}
.f-head{display:flex;align-items:center;gap:22px}
.f-title{font-family:'Montserrat',sans-serif;font-size:19px;color:var(--white)}
.f-text{font-size:14px;color:var(--white);line-height:1.75;text-align:center}
.social{top:3612px;width:26px;height:26px;background:var(--gold);border:2px solid #9c7c2e}
.copyright{left:0;width:1200px;top:3664px;text-align:center;font-size:13px;color:var(--white)}
</style>
</head>
<body>

<!-- top bar -->
<div class="abs topbar"></div>
<div class="abs contact-chip" style="left:77px">
  <div class="chip-icon"><svg width="24" height="24" viewBox="0 0 24 24"><path d="M6.6 10.8a15 15 0 0 0 6.6 6.6l2.2-2.2c.3-.3.7-.4 1-.2 1.1.4 2.3.6 3.6.6.6 0 1 .4 1 1V20c0 .6-.4 1-1 1A17 17 0 0 1 3 4c0-.6.4-1 1-1h3.5c.6 0 1 .4 1 1 0 1.3.2 2.5.6 3.6.1.3 0 .7-.2 1z" fill="#333"/></svg></div>
  <span>info@kelto.example</span>
</div>
<div class="abs contact-chip" style="left:897px">
  <span>+1 234 555 0192</span>
  <div class="chip-icon"><svg width="24" height="24" viewBox="0 0 24 24"><path d="M6.6 10.8a15 15 0 0 0 6.6 6.6l2.2-2.2c.3-.3.7-.4 1-.2 1.1.4 2.3.6 3.6.6.6 0 1 .4 1 1V20c0 .6-.4 1-1 1A17 17 0 0 1 3 4c0-.6.4-1 1-1h3.5c.6 0 1 .4 1 1 0 1.3.2 2.5.6 3.6.1.3 0 .7-.2 1z" fill="#333"/></svg></div>
</div>
<div class="abs logo"><span class="big">KELTO</span><span class="small">CONSTRUCTION</span></div>

<!-- nav -->
<nav class="abs nav">
  <ul>
    <li class="active">HOME</li><li>ABOUT</li><li>OUR PROJECTS</li><li>LATEST BLOG</li><li>CONTACT US</li>
  </ul>
</nav>
<div class="abs search"><svg width="22" height="22" viewBox="0 0 22 22"><circle cx="9" cy="9" r="6" fill="none" stroke="#b8963e" stroke-width="2"/><line x1="13.5" y1="13.5" x2="19" y2="19" stroke="#b8963e" stroke-width="2"/></svg></div>

<!-- hero -->
<div class="abs hero" role="img" aria-label="Construction site with tower cranes and concrete frame"></div>
<h1 class="abs hero-title">VIRTULITY BUILD YOUR DREAM</h1>
<p class="abs hero-text">Lorem Ipsum is simply dummy text of the printing and typesetting industry. Lorem Ipsum has been the industry's standard dummy text ever since the 1500s.</p>
<div class="abs arrow-btn" style="left:57px;top:472px"><svg width="14" height="14" viewBox="0 0 14 14"><path d="M10 1 4 7l6 6" fill="none" stroke="#fff" stroke-width="3"/></svg></div>
<div class="abs arrow-btn" style="left:1103px;top:472px"><svg width="14" height="14" viewBox="0 0 14 14"><path d="m4 1 6 6-6 6" fill="none" stroke="#fff" stroke-width="3"/></svg></div>

<!-- feature panels -->
<svg class="abs" style="left:0;top:0" width="1200" height="1060" viewBox="0 0 1200 1060">
  <rect x="77" y="903" width="1046" height="155" fill="#333"/>
  <polygon points="77,793 424,764 424,903 77,903" fill="#b8963e"/>
  <polygon points="773,764 1123,793 1123,903 773,903" fill="#b8963e"/>
  <polygon points="424,752 598,740 773,752 773,938 598,952 424,938" fill="#c9a756"/>
</svg>
<div class="abs feature" style="left:93px;top:798px;width:320px">
  <div class="feature-icon" role="img" aria-label="Team meeting icon"></div>
  <div><h3>Communicate<br>professionalism</h3><p>Lorem Ipsum is simply printing and typesetting industry.</p></div>
</div>
<div class="abs feature" style="left:452px;top:798px;width:315px">
  <div class="feature-icon" role="img" aria-label="Worker in hard hat icon"></div>
  <div><h3>High quality wormanship</h3><p>Lorem Ipsum is simply printing and typesetting industry.Lorem Ipsum has been the industry's</p></div>
</div>
<div class="abs feature" style="left:790px;top:798px;width:320px">
  <div class="feature-icon" role="img" aria-label="Award badge icon"></div>
  <div><h3 style="margin-top:8px">Quality service</h3><p>Lorem Ipsum is simply printing and typesetting industry.</p></div>
</div>
<div class="abs band-text">WE HAVE COMPLETED LOT OF PROJECTS . YOU CAN HIRE US FOR YOUR FUTURE PROJECTS.</div>

<!-- welcome -->
<section class="abs welcome"></section>
<h2 class="abs welcome-title">Welcome to <span class="gold">KELTO</span> Construction</h2>
<p class="abs welcome-text">Lorem Ipsum is simply dummy text of the printing and typesetting industry. Lorem Ipsum has been the industry's standard dummy text ever since the 1500s, when an unknown printer took a galley of type and scrambled it to make a type specimen book. It has survived not only five centuries, but also the leap into electronic typesetting, remaining essentially unchanged. It was popularised in the 1960s with the release of Letraset sheets containing Lorem Ipsum passages</p>
<div class="abs btn btn-gold" style="left:77px;top:1345px;width:158px;height:60px">READ MORE</div>
<div class="abs welcome-art"><div class="welcome-art-fill" role="img" aria-label="Illustration of a modern office building"></div></div>

<!-- projects -->
<section class="abs projects" role="img" aria-label="Dark construction site backdrop"></section>
<div class="abs kicker">THE PROJECTS</div>
<h2 class="abs projects-title">WE ALREADY COMPLETED</h2>
<div class="abs arrow-btn" style="left:1028px;top:1584px"><svg width="14" height="14" viewBox="0 0 14 14"><path d="M10 1 4 7l6 6" fill="none" stroke="#fff" stroke-width="3"/></svg></div>
<div class="abs arrow-btn" style="left:1083px;top:1584px"><svg width="14" height="14" viewBox="0 0 14 14"><path d="m4 1 6 6-6 6" fill="none" stroke="#fff" stroke-width="3"/></svg></div>
<div class="abs photo" style="left:0;background:linear-gradient(160deg,#e8e6e0,#b9b4aa 60%,#3a3631)" role="img" aria-label="Completed project: open-plan dining room"></div>
<div class="abs photo" style="left:300px;background:linear-gradient(160deg,#f2f2f0,#dcd9d2 60%,#8a6a48)" role="img" aria-label="Completed project: bright living room"></div>
<div class="abs photo" style="left:600px;background:linear-gradient(160deg,#8c8178,#cfc6bb 55%,#6f5f52)" role="img" aria-label="Completed project: bedroom interior"></div>
<div class="abs photo" style="left:900px;background:linear-gradient(160deg,#d8e0e4,#9fa8a6 55%,#5b5a52)" role="img" aria-label="Completed project: terrace with sea view"></div>

<!-- testimonials -->
<section class="abs testi"></section>
<h2 class="abs section-title" style="top:2015px">Client <span class="gold">TESTIMONIAL</span></h2>
<svg class="abs" style="left:0;top:2090px" width="1200" height="230" viewBox="0 0 1200 230">
  <polygon points="77,8 591,22 591,218 77,210" fill="#333"/>
  <polygon points="611,22 1123,8 1123,210 611,218" fill="#333"/>
</svg>
<div class="abs quote-box" style="left:108px;top:2145px">&ldquo;</div>
<div class="abs" style="left:185px;top:2135px;width:380px">
  <p class="testi-text">Lorem Ipsum is simply dummy text of the printing and typesetting industry. Lorem Ipsum has been the industry's standard dummy text ever since the 1500s,</p>
  <p class="testi-name">ARIN HOLT , CEO</p>
</div>
<div class="abs quote-box" style="left:1038px;top:2145px">&rdquo;</div>
<div class="abs" style="left:650px;top:2135px;width:370px;text-align:center">
  <p class="testi-text">Lorem Ipsum is simply dummy text of the printing and typesetting industry. Lorem Ipsum has been the industry's standard dummy text ever since the 1500s,</p>
  <p class="testi-name" style="text-align:right">ARIN HOLT , CEO</p>
</div>
<div class="abs dot" style="left:562px"></div>
<div class="abs dot" style="left:580px"></div>
<div class="abs dot" style="left:598px;background:var(--gold)"></div>
<div class="abs dot" style="left:616px"></div>

<!-- blog -->
<h2 class="abs section-title" style="top:2517px">Recent <span class="gold">BLOG</span></h2>
<div class="abs" style="left:107px;top:2605px;width:492px;height:289px;background:linear-gradient(135deg,#7a7f86,#d8c23c 45%,#e8e8e8 70%,#8e8a80);clip-path:polygon(0 0,100% 0,100% 100%,0 96%)" role="img" aria-label="Engineers reviewing plans on a tablet"></div>
<div class="abs" style="left:599px;top:2615px;width:524px;height:272px;background:var(--gold);clip-path:polygon(0 0,100% 0,100% 100%,0 96%)"></div>
<div class="abs blog-card" style="left:627px;top:2643px;width:455px">
  <h3>Low Cost Construction Tips &amp; Tricks</h3>
  <div class="meta"><span><i style="background:#fff"></i>By Admin</span><span><i style="background:#fff"></i>19 March 2018</span><span><i style="background:#fff"></i>10 Comments</span></div>
  <p>Lorem Ipsum is simply dummy text of the printing and typesetting industry. Loremindustry's standard dummy text ever since the 1500s.</p>
  <div class="btn btn-dark" style="width:134px;height:48px;font-size:16px;margin-top:14px">READ MORE</div>
</div>
<div class="abs" style="left:77px;top:2904px;width:522px;height:274px;background:var(--dark);clip-path:polygon(0 0,100% 2%,100% 100%,0 100%)"></div>
<div class="abs blog-card" style="left:132px;top:2930px;width:455px">
  <h3>Low Cost Construction Tips &amp; Tricks</h3>
  <div class="meta"><span style="color:#b8963e"><i style="background:#b8963e"></i>By Admin</span><span style="color:#b8963e"><i style="background:#b8963e"></i>19 March 2018</span><span style="color:#b8963e"><i style="background:#b8963e"></i>10 Comments</span></div>
  <p>Lorem Ipsum is simply dummy text of the printing and typesetting industry. Loremindustry's standard dummy text ever since the 1500s.</p>
  <div class="btn btn-gold" style="width:134px;height:48px;font-size:16px;margin-top:14px">READ MORE</div>
</div>
<div class="abs" style="left:599px;top:2897px;width:524px;height:292px;background:linear-gradient(135deg,#a0785a,#d9b430 40%,#b0352a 65%,#4a3e36);clip-path:polygon(0 0,100% 0,100% 96%,0 100%)" role="img" aria-label="Builder holding a yellow hard hat"></div>

<!-- call to action -->
<section class="abs cta"></section>
<p class="abs cta-text">Looking for a 100% quality and affordable constructor company for your project?</p>
<div class="abs btn btn-dark" style="left:966px;top:3321px;width:157px;height:62px">CONTACT US</div>

<!-- footer -->
<footer class="abs footer"></footer>
<svg class="abs" style="left:0;top:3428px" width="1200" height="170" viewBox="0 0 1200 170">
  <polygon points="77,0 424,0 424,142 250,157 77,142" fill="#333"/>
  <polygon points="424,0 773,0 773,142 598,157 424,142" fill="#3d3d3d"/>
  <polygon points="773,0 1123,0 1123,142 948,157 773,142" fill="#333"/>
</svg>
<div class="abs f-col" style="left:77px;width:347px">
  <div class="f-head"><svg width="20" height="20" viewBox="0 0 24 24"><path d="M6.6 10.8a15 15 0 0 0 6.6 6.6l2.2-2.2c.3-.3.7-.4 1-.2 1.1.4 2.3.6 3.6.6.6 0 1 .4 1 1V20c0 .6-.4 1-1 1A17 17 0 0 1 3 4c0-.6.4-1 1-1h3.5c.6 0 1 .4 1 1 0 1.3.2 2.5.6 3.6.1.3 0 .7-.2 1z" fill="#b8963e"/></svg><span class="f-title">Call Us Now</span></div>
  <div class="f-text">+1 234 555 0192</div>
</div>
<div class="abs f-col" style="left:424px;width:349px">
  <div class="f-head"><svg width="18" height="22" viewBox="0 0 18 24"><path d="M9 0a9 9 0 0 0-9 9c0 7 9 15 9 15s9-8 9-15a9 9 0 0 0-9-9zm0 12.5A3.5 3.5 0 1 1 9 5.5a3.5 3.5 0 0 1 0 7z" fill="#b8963e"/></svg><span class="f-title">Our Location</span></div>
  <div class="f-text">123 Building Name, Street,<br>City, Country - Zip code</div>
</div>
<div class="abs f-col" style="left:773px;width:350px">
  <div class="f-head"><svg width="20" height="16" viewBox="0 0 20 16"><rect x="1" y="1" width="18" height="14" fill="#b8963e"/><path d="M1 1l9 8 9-8" fill="none" stroke="#333" stroke-width="1.5"/></svg><span class="f-title">Mail Us Now</span></div>
  <div class="f-text">info@kelto.example</div>
</div>
<div class="abs social" style="left:540px"></div>
<div class="abs social" style="left:570px"></div>
<div class="abs social" style="left:600px"></div>
<div class="abs social" style="left:630px"></div>
<div class="abs copyright">Copyright © 2018, <b>KELTO CONSTRUCTION</b> . All rights reserved. Privacy Policy.</div>

</body>
</html>
```